Introduction flyer

Brightpath Dietetics & Vitality Advisory, is a new holistic nutritional therapy specialising in womens health. I want a flyer that appeals to women between 15 to 60. It must speak "health, food & balance". I have attached the basic info I need included in the text. I like Greens & Blues, soft text. My flyer will be distributed to cafes, shops, fitness centres, hung up in grocery stores & health centres etc. The QELR & HPVA logos need to appear on the flyer to show I am fully registered. My own logo & company name is attached.

Target Market(s)

Women from 10 to 60 years old.

Industry/Entity Type

Nutritionist

Colors
32a6d7
abd037
33b8a4
fbf289
ffcf3e
b768aa
d5d5d5
dcdcdc
e8e8e8

Requirements
Must have
• An image of healthy food & ladies. A group of women eating soup, stews or curry type dishes, with plenty of colour - no bread or white wine, and not just fruit please. Food that looks enjoyable to the average person.
• Nutrition is main part of my job, so please keep that in mind & emphasise food & natural well being.
Should not have
• People exercising, men, white wine, bread, cakes, sweets etc..

```html
<!DOCTYPE html>
<html lang="en">
<head>
<meta charset="utf-8">
<title>Brightpath Dietetics &amp; Vitality Advisory – Introduction Flyer</title>
<link rel="stylesheet" href="https://fonts.googleapis.com/css2?family=Bitter:wght@400;500;600&family=Cinzel:wght@400;500&family=Raleway:wght@700&family=Cabin:ital,wght@0,400;0,500;1,400&family=Exo+2:wght@400&display=swap">
<style>
  :root{
    --page-bg:#ecebe8;
    --paper:#f7f7f7;
    --brand-blue:#2b6fbf;
    --badge-blue:#3a8ad4;
    --brand-green:#17963a;
    --leaf-green:#1aa84a;
    --text-dark:#333;
    --photo-light:#eef6dc;
    --photo-mid:#c9e28f;
    --photo-deep:#9ccd63;
  }
  *{margin:0;padding:0;box-sizing:border-box}
  html,body{width:1200px;height:1200px;overflow:hidden;background:var(--page-bg)}
  .stage{position:relative;width:1200px;height:1200px}
  .flyer{
    position:absolute;left:190px;top:20px;width:890px;height:1258px;
    transform:scale(0.922);transform-origin:top left;
    background:var(--paper);overflow:hidden;
    box-shadow:0 6px 20px rgba(0,0,0,.18);
    font-family:"Cabin",sans-serif;color:var(--text-dark);
  }
  .flyer-art{position:absolute;left:0;top:0;width:890px;height:1258px}
  .abs{position:absolute}

  .brand{left:520px;top:40px;width:360px;text-align:center}
  .brand-mark{width:92px;height:92px;border-radius:50%;background:var(--brand-blue);margin:0 auto 26px}
  .brand-name{font-family:"Cinzel",serif;font-size:19px;color:var(--brand-blue);letter-spacing:.5px;line-height:22px;white-space:nowrap}
  .brand-sub{font-family:"Cinzel",serif;font-size:14px;color:var(--brand-blue);letter-spacing:2px;line-height:20px;white-space:nowrap}
  .badges{left:610px;top:226px;display:flex;gap:22px}
  .badge-shape{width:82px;height:26px;border-radius:13px;background:#5b4aa0}
  .badge-shape.alt{background:var(--leaf-green);border-radius:4px;width:70px}

  .offer{left:580px;top:460px;width:250px;height:250px;display:flex;align-items:center;justify-content:center;text-align:center;
    font-family:"Exo 2",sans-serif;color:#fff;font-size:20.5px;line-height:25px}

  .headline{left:53px;top:545px;width:520px}
  .h-do{font-family:"Cinzel",serif;font-weight:500;font-size:52px;color:var(--brand-green);line-height:56px}
  .h-energy{font-family:"Bitter",serif;font-size:28px;color:var(--brand-blue);line-height:38px;letter-spacing:.3px}
  .h-cycle{font-family:"Raleway",sans-serif;font-weight:700;font-size:31px;color:var(--brand-green);line-height:38px;letter-spacing:.2px}
  .h-baby{font-family:"Bitter",serif;font-size:27px;color:var(--brand-blue);line-height:36px;letter-spacing:.3px}

  .tagline{left:53px;top:737px;font-family:"Bitter",serif;font-weight:500;font-size:23px;color:var(--brand-green);letter-spacing:.6px}
  .motto{left:53px;top:772px;font-size:28px;color:#444}
  .intro{left:53px;top:812px;width:783px;font-size:14px;line-height:18px;text-align:justify;color:#3a3a3a}

  .services{left:53px;top:901px;width:430px}
  .services h2{font-family:"Cabin",sans-serif;font-weight:500;font-size:18px;line-height:22px;color:var(--brand-green)}
  .services ul{list-style:none;margin-top:18px}
  .services li{position:relative;padding-left:22px;font-size:14.5px;line-height:18px;margin-bottom:3px;color:#3a3a3a}
  .services li::before{content:"»";position:absolute;left:0;top:-2px;font-size:18px;font-weight:700;color:var(--brand-blue)}

  .col-divider{left:504px;top:918px;width:1px;height:290px;background:#9fb5d6}

  .contact{left:540px;top:900px;width:300px;text-align:center}
  .contact-call{font-family:"Cinzel",serif;font-size:20px;color:var(--brand-blue);letter-spacing:.4px}
  .icon{display:block;margin:6px auto 0}
  .contact-phone{font-size:22px;color:#333;letter-spacing:.5px;line-height:26px}
  .contact-email{font-size:16px;color:#333;line-height:20px}
  .contact-book{font-family:"Cinzel",serif;font-size:17px;color:var(--brand-green);line-height:21.5px;margin-top:20px;letter-spacing:.3px}
  .contact-note{font-style:italic;font-size:13.5px;line-height:18px;color:#444;margin-top:14px;text-align:justify;text-align-last:center}
</style>
</head>
<body>
<div class="stage">
  <article class="flyer">
    <svg class="flyer-art" viewBox="0 0 890 1258">
      <defs>
        <radialGradient id="photoGlow" cx="0.55" cy="0.4" r="0.75">
          <stop offset="0" stop-color="var(--photo-light)"/>
          <stop offset="0.6" stop-color="var(--photo-mid)"/>
          <stop offset="1" stop-color="var(--photo-deep)"/>
        </radialGradient>
        <linearGradient id="swoosh" x1="0" y1="0" x2="1" y2="0">
          <stop offset="0" stop-color="#3b78cc"/>
          <stop offset="1" stop-color="#2a5fb0"/>
        </linearGradient>
      </defs>
      <path role="img" aria-label="Photo of a smiling woman drinking a glass of water behind a spread of fresh fruit and vegetables"
            d="M0 0 H890 V330 C840 420 760 480 590 520 C420 520 200 420 0 270 Z" fill="url(#photoGlow)"/>
      <path d="M0 0 H60 C30 20 10 45 0 70 Z" fill="var(--badge-blue)"/>
      <path d="M845 0 H890 V70 C880 40 865 18 845 0 Z" fill="var(--leaf-green)"/>
      <path d="M0 270 C200 420 420 520 600 524 L590 575 C380 560 170 470 0 390 Z" fill="url(#swoosh)"/>
      <path d="M0 392 C170 472 380 562 590 577 L575 560 C380 548 180 470 0 400 Z" fill="#fff" opacity=".8"/>
      <path d="M890 230 V450 C840 470 790 500 760 540 C790 470 830 380 890 230 Z" fill="var(--leaf-green)"/>
      <path d="M800 640 C830 660 845 690 848 725 C835 690 815 670 790 660 Z" fill="var(--brand-blue)"/>
      <circle cx="705" cy="585" r="132" fill="var(--badge-blue)"/>
      <circle cx="705" cy="585" r="122" fill="none" stroke="#fff" stroke-width="1.5" stroke-dasharray="5 4"/>
      <rect x="0" y="1231" width="890" height="27" fill="var(--brand-blue)"/>
    </svg>

    <div class="abs brand">
      <div class="brand-mark"></div>
      <div class="brand-name">Brightpath Dietetics</div>
      <div class="brand-sub">&amp; Vitality Advisory</div>
    </div>
    <div class="abs badges" aria-label="Registration badges">
      <div class="badge-shape"></div>
      <div class="badge-shape alt"></div>
    </div>

    <div class="abs offer">HOME VISITS<br>available,<br>AT NO EXTRA COST<br>within local area;<br>I can visit<br>your place of work<br>OR HOME.</div>

    <header class="abs headline">
      <div class="h-do">Do you</div>
      <div class="h-energy">experience low energy, low libido,</div>
      <div class="h-cycle">menstrual cycle complications</div>
      <div class="h-baby">OR ARE YOU PLANNING A BABY?</div>
    </header>

    <p class="abs tagline">Small changes to your diet may lead to big changes in your health.</p>
    <p class="abs motto">Eat well, live well.</p>
    <p class="abs intro">Discover exactly what YOU need to change and how to make these changes long lasting. There is no 1 rule-fits-all. My nutritional advice aims to dig up the root cause to my client’s health concerns. My lifestyle plans are completely personalised to an individual’s needs and circumstances. I consider the whole person not just symptoms or disease.</p>

    <section class="abs services">
      <h2>Qualified, Registered and fully insured Nutritional Therapist &amp; Wellness Consultant, specialising in:</h2>
      <ul>
        <li>Fertility, IVF, pre-conception, pregnancy &amp; post-natal care</li>
        <li>Menstrual cycle challenges<br>(PCOS, Endometriosis, PMS, heavy/irregular periods etc)</li>
        <li>Thyroid conditions</li>
        <li>Low libido</li>
        <li>Digestive health</li>
        <li>Chronic fatigue syndrome</li>
        <li>Perimenopause/menopause</li>
        <li>Weight management</li>
        <li>Type 2 diabetes, blood sugar dysregulation, high blood pressure, high cholesterol</li>
        <li>Recurring infections e.g. thrush, UTIs, coughs, colds</li>
      </ul>
    </section>

    <div class="abs col-divider"></div>

    <section class="abs contact">
      <div class="contact-call">CALL MAEVE TODAY ON</div>
      <svg class="icon" width="22" height="20" viewBox="0 0 24 24" aria-hidden="true">
        <path d="M6.6 10.8a15 15 0 0 0 6.6 6.6l2.2-2.2a1 1 0 0 1 1-.25 11.4 11.4 0 0 0 3.6.57 1 1 0 0 1 1 1V20a1 1 0 0 1-1 1A17 17 0 0 1 3 4a1 1 0 0 1 1-1h3.5a1 1 0 0 1 1 1c0 1.250.2 2.450.57 3.57a1 1 0 0 1-.25 1z" fill="var(--brand-blue)"/>
      </svg>
      <div class="contact-phone">085-555-0142</div>
      <svg class="icon" width="22" height="16" viewBox="0 0 24 16" aria-hidden="true">
        <rect x="1" y="1" width="22" height="14" rx="2" fill="none" stroke="var(--brand-blue)" stroke-width="2"/>
        <path d="M1 2 L12 9 L23 2" fill="none" stroke="var(--brand-blue)" stroke-width="2"/>
      </svg>
      <div class="contact-email">maeve@brightpathdietetics.ie</div>
      <div class="contact-book">TO BOOK A CONSULTATION OR<br>FOR A FREE NO OBLIGATION<br>15-minute MINI CONSULTATION</div>
      <p class="contact-note">Initial consultations typically last up to 2 hours, follow-ups 30 – 60 minutes. Further investigative tests may be recommended such as blood, urine, saliva sampling. These will always be agreed with the client in advance.</p>
    </section>
  </article>
</div>
</body>
</html>
```